Stationery for Villa Marenta Design Hotel**

Who we are:

Wander on an isolated beach while breathing in the fresh, salty, sea air. Listen to the warm Pacific wind rustling through green palm trees as you walk to a pristine lagoon. Feel the delicious warmth of the sun kiss your skin; the beach is yours. At Villa Marenta you can experience a vacation in undisturbed, natural beauty. We have created a place for you to find new strength, relaxation, and inner harmony. We offer total rest to the experienced traveler from all over the world.

We are a brand new and smartly built design-hotel (under construction) close to a unique beach and a fantastic surf spot in Huatulco, Southwest Mexico.

As you can see in the attachments, we do have an established corporate design, but as for now still need a format for booklets for information around our hotel and things to do in the area, important numbers (we fill in the content for that one).

Our corporate colors:
green #64b445, brown #b07043, blue #0ab7cf, yellow # f9b02a and #fcc01a, navy #444f69
Corporate fonts:
Krub and Miller Banner.
For further information access:
www.villamarenta.example
https://slidevault.example/view/QmPxLwZrTyKsNbVcHdJe/

Social Media: VillaMarenta

Industry/Entity Type

Hotel

Font styles to use
Other font styles liked:
• Krub, Miller Banner

Requirements
Must have
• Stick to Logo Design, defined corporate elements, logo, colors, fonts and general touch and feel
Nice to have
• Who we are:

Our corporate colors:
Corporate fonts:
Krub and Miller Banner.
www.villamarenta.example

Social Media: VillaMarenta

```html
<!DOCTYPE html>
<html lang="en">
<head>
<meta charset="utf-8">
<title>Villa Marenta – Letterhead</title>
<link rel="stylesheet" href="https://fonts.googleapis.com/css2?family=Tinos:wght@400&display=swap">
<style>
  :root {
    --backdrop: #d7dcdc;
    --paper: #ffffff;
    --teal: #0a9aa6;
    --teal-dark: #077f89;
    --sun: #f9b02a;
    --ink: #555a66;
    --rule: #c9cdd2;
    --leaf-light: #e4efd9;
    --leaf-mid: #d3e6c4;
  }
  * { box-sizing: border-box; margin: 0; padding: 0; }
  html, body {
    width: 1200px; height: 784px; overflow: hidden;
    background: var(--backdrop);
  }
  .letterhead {
    position: absolute;
    left: 110px; top: 40px;
    width: 980px; height: 704px;
    background: var(--paper);
    box-shadow: 0 6px 18px rgba(0,0,0,.12);
    overflow: hidden;
  }
  .top-band {
    position: absolute; left: 0; right: 0; top: 18px; height: 12px;
    background: linear-gradient(180deg, var(--teal) 0%, var(--teal-dark) 100%);
  }
  .brand {
    position: absolute; top: 56px; right: 60px;
    display: flex; align-items: center; gap: 12px;
  }
  .brand-square {
    width: 30px; height: 30px; border: 2px solid var(--sun);
  }
  .brand-name {
    font-family: "Tinos", serif;
    font-size: 28px; font-weight: 400; letter-spacing: .04em;
    color: var(--sun);
  }
  .contact {
    position: absolute; top: 282px; right: 60px;
    border-left: 1px solid var(--rule);
    padding-left: 12px;
    font-family: "Tinos", serif;
    font-size: 14px; line-height: 19px; color: var(--ink);
    list-style: none;
  }
  .contact li { display: flex; align-items: flex-start; gap: 8px; }
  .contact svg { flex: none; width: 12px; height: 12px; margin-top: 3px; }
  .leaf-decor {
    position: absolute; left: 210px; bottom: -40px;
    width: 330px; height: 300px;
    border-radius: 55% 45% 40% 60% / 55% 50% 50% 45%;
    background: radial-gradient(circle at 45% 45%, var(--leaf-mid) 0%, var(--leaf-light) 60%, rgba(228,239,217,0) 100%);
    opacity: .8;
  }
</style>
</head>
<body>
  <main class="letterhead">
    <div class="top-band"></div>

    <header class="brand">
      <span class="brand-square"></span>
      <span class="brand-name">Villa Marenta</span>
    </header>

    <ul class="contact">
      <li>
        <svg viewBox="0 0 12 12"><circle cx="6" cy="6" r="6" fill="#0a9aa6"/><path d="M6 2.6a2 2 0 0 0-2 2c0 1.5 2 4 2 4s2-2.5 2-4a2 2 0 0 0-2-2z" fill="#fff"/></svg>
        <span>Villa Marenta, Playa Serena,<br>Costa Azul, Marenia, Solterra</span>
      </li>
      <li>
        <svg viewBox="0 0 12 12"><circle cx="6" cy="6" r="6" fill="#0a9aa6"/><path d="M4 3.2l1.2 1.3-.6.8c.4.8 1 1.4 1.8 1.8l.8-.6L8.5 7.8 7.8 8.8C5.6 8.4 3.6 6.4 3.2 4.2z" fill="#fff"/></svg>
        <span>+52 1 (555) 010 4477</span>
      </li>
      <li>
        <svg viewBox="0 0 12 12"><circle cx="6" cy="6" r="6" fill="#0a9aa6"/><rect x="3" y="4" width="6" height="4.2" fill="#fff"/><path d="M3 4l3 2.3L9 4" fill="none" stroke="#0a9aa6" stroke-width=".7"/></svg>
        <span>hello@villamarenta.example</span>
      </li>
      <li>
        <svg viewBox="0 0 12 12"><circle cx="6" cy="6" r="6" fill="#0a9aa6"/><circle cx="6" cy="6" r="3" fill="none" stroke="#fff" stroke-width=".8"/><path d="M3 6h6M6 3c-1.2 1.6-1.2 4.4 0 6M6 3c1.2 1.6 1.2 4.4 0 6" fill="none" stroke="#fff" stroke-width=".6"/></svg>
        <span>www.villamarenta.example</span>
      </li>
    </ul>

    <div class="leaf-decor" role="img" aria-label="Faint pale green watercolour monstera leaf"></div>
  </main>
</body>
</html>
```